LADIES' HARBOR COLLECTIVE

Design a website for a membership based organization focusing on entrepreneurship, women's issues and global news regarding commerce.
Also, want a news daily tie in to site, and social media outlets.
I want the colors in strong blue, deep or metallic gold and cream/white like logo which will be provided. I want logo altered with globe to replace small sphere in the design.
Also, board members page that should be redesigned. Might need extra coding.
PLEASE SEE http://ladiesharborcollective.example DIDN'T LIKE THIS LAY OUT AT ALL TOO MUCH WHITE AND NOT ENOUGH IMPACT. WANT TO DRAW MEMBERS.

PLEASE SEE http://www.qrtv-sample.example/Index.cfm BUT THIS IS WAY TO BUSY BUT I LIKE THE SLIDING.

SEE OUR TWITTER ACCOUNT FOR INSIGHT. @LADIESHARBCOL

Reason: Happy Holidays. The board approving the design will be out on season time vacation until Jan. 2. Please make any edits requested from designer already submitting layouts. Thank you, Odette

Target Market(s)

GLOBAL BUSINESS WOMEN AND ENTREPRENEURS AGES 20-65

Industry/Entity Type

Media

Number of Pages Required

4 page

Font styles to use
Other font styles liked:
• Baskerville or something similar

Colors
fbed22
3377b5
9bcb3c

Requirements
Must have
• Show diversity of ethnicities if using stock photos. Vibrant and inviting site, MUST JOIN or Be part of this organization. Luxury style
• THIS IS A FOR PROFIT WEBSITE.
• Membership Fees:
• Annual Fee $250
• For an additional fee of $150 you can grow your visibility and voice through our Ladies' Harbor Collective Bulletin and Speaker's Bureau (LHCBSB).
• LHC Speaker's Bureau will support your personal, business and organizations' objectives and to give you greater visibility and voice as an authority world leader or business visionary in your field of service.
• LHCSB realizes that so many worthy leaders' in diverse fields of service are never allowed to be heard. If you feel you are a dynamic speaker, run a worthwhile business or organization and whose wisdom and success can be of service of others sign up today and be part of the LHCSB!
• Student Membership
• Discounted student memberships are also available. Students have access to selected group forums, as well as selected groups of members that provide mentoring. Mentoring helps continue the member's legacy and creates a well spring of future leaders. Student membership fees cost just $75 a year.
• Contact us to help promote you and other women's vision throughout the world.
• Join LHC Now!
• CAN YOU PROVIDE A HEADLINE WITHOUT WOMEN SEE TWITTER ACCOUNT.
Nice to have
• Nice headline and well position tabs.
• Home
• Join LHC Now
• Memberships
• LHC Team Leadership
• About Us
• Contact
• LHC is an Effective Women's Initiative for You!
• New Member - Women's Organization
• 20% Discount- Offer Valid on Your Membership Fee When You Join before 1/30/2105
• Memberships
• LHC Leadership
• At Ladies' Harbor Collective, we offer the opportunity to connect with women throughout the globe. Join these trailblazers to shorten your path to success and camaraderie.
• Who We Are
• Ladies' Harbor Collective is an online women's initiative that promotes your business and visions through social engagement. We are here to help you form strategic partnerships with like-minded women around the world. End your solo journey by becoming a member of LHC.
• LHC also features a forum to promote the services, campaigns, and social activism by our members.
• LHC is about women helping other women. Contact us for more information.
• Learn More about Ladies' Harbor Collective
• Contact us for more information in regards to LHC membership and how to get involved.
• SHARE THIS PAGE:
• twitter, fb, instagram, etc.

```html
<!DOCTYPE html>
<html lang="en">
<head>
<meta charset="utf-8">
<title>Ladies' Harbor Collective</title>
<link href="https://fonts.googleapis.com/css2?family=Open+Sans:wght@300;400;600&display=swap" rel="stylesheet">
<style>
:root{
  --blue:#1b4e8c;
  --blue-bright:#1f7fc4;
  --dot-blue:#3fb4f0;
  --gold:#d9a318;
  --yellow:#fbc02d;
  --ink:#444;
  --muted:#777;
  --card:#eeeeee;
  --footer:#1c1c1e;
  --footer-bottom:#141414;
  --white:#fff;
}
*{margin:0;padding:0;box-sizing:border-box}
html,body{width:1004px;height:1200px;overflow:hidden;background:var(--white)}
body{position:relative;font-family:'Open Sans',Arial,sans-serif;color:var(--ink)}
.abs{position:absolute}
.top-rule{left:0;top:0;width:1004px;height:2px;background:var(--blue-bright)}
.brand{left:84px;top:44px;display:flex;align-items:center;gap:8px}
.brand-mark{width:18px;height:18px;border-radius:50%;background:var(--gold)}
.brand-name{font-size:13px;font-weight:600;color:var(--blue)}
.main-nav a{position:absolute;top:53px;font-size:11px;color:#444;text-decoration:none;white-space:nowrap}
.main-nav a.active{color:var(--gold)}
.hero{left:0;top:111px;width:1004px;height:387px;
  background:radial-gradient(ellipse 190px 230px at 502px 200px,#d8c4ae 0%,#bfb2a4 45%,rgba(160,160,160,0) 100%),
  linear-gradient(90deg,#8c8f92 0%,#b8b9b8 30%,#c9c6c2 50%,#b0b3b6 72%,#7f8790 100%)}
.hero h1{position:absolute;left:0;width:1004px;top:182px;text-align:center;color:var(--white);
  font-size:29px;font-weight:600;line-height:43px;text-transform:uppercase}
.dots span{position:absolute;top:284px;width:10px;height:10px;border-radius:50%;background:var(--dot-blue)}
.dots span.on{background:var(--yellow)}
.intro{left:0;width:1004px;top:522px;text-align:center;color:var(--blue);font-size:14.5px;font-weight:600;line-height:26px}
.card{top:602px;width:358px;height:126px;background:var(--card)}
.card-icon{position:absolute;left:35px;top:24px;width:79px;height:79px;background:var(--white);display:flex;align-items:center;justify-content:center}
.card h3{position:absolute;left:129px;top:36px;font-size:17.5px;font-weight:400;color:var(--blue)}
.card p{position:absolute;left:131px;top:68px;width:222px;font-size:9.2px;line-height:14.5px;color:var(--muted);font-weight:300}
.who{left:0;width:1004px;top:757px;text-align:center;color:var(--blue);font-size:14.5px;font-weight:600}
.who-text{left:100px;width:804px;top:790px;text-align:center;font-size:9.6px;line-height:20px;color:var(--muted)}
.read-more{left:454px;top:869px;width:96px;height:33px;border:1px solid #ddd;border-radius:3px;font-size:10.5px;color:#666;display:flex;align-items:center;justify-content:center}
.footer{left:0;top:934px;width:1004px;height:208px;background:var(--footer);color:#ddd}
.footer-bottom{left:0;top:1142px;width:1004px;height:58px;background:var(--footer-bottom)}
.foot-brand{left:84px;top:962px;font-size:10px;font-weight:600;color:#bbb}
.foot-about{left:83px;top:996px;width:182px;font-size:10px;line-height:20px;color:#eee}
.social span{position:absolute;top:1077px;width:10px;height:10px;border:1px solid #888;border-radius:50%}
.foot-title{top:951px;font-size:13.5px;color:var(--white);font-weight:400}
.tweet{left:277px;width:220px;font-size:9.6px;line-height:18.5px;color:#eee}
.tweet-dot{position:absolute;left:0;top:4px;width:11px;height:11px;border-radius:50%;background:#666}
.tweet p{margin-left:23px}
.tweet .when{color:var(--yellow)}
.thumb{width:55px;height:42px;border-radius:2px}
.news-text{left:718px;top:983px;width:200px;font-size:9.6px;line-height:18.5px;color:#eee}
.email{left:720px;top:1050px;width:202px;height:30px;border:1px solid #777;font-size:9px;color:#bbb;padding:0 8px;display:flex;align-items:center}
.subscribe{left:862px;top:1090px;width:58px;height:24px;background:var(--yellow);border-radius:3px;color:#222;font-size:8.5px;display:flex;align-items:center;justify-content:center}
.copyright{left:83px;top:1165px;font-size:9px;color:#bbb}
.foot-nav a{position:absolute;top:1165px;font-size:8.5px;color:#888;text-decoration:none;white-space:nowrap}
</style>
</head>
<body>
<div class="abs top-rule"></div>

<header>
  <div class="abs brand"><span class="brand-mark"></span><span class="brand-name">Ladies' Harbor Collective</span></div>
  <nav class="main-nav">
    <a class="active" style="left:353px">HOME</a>
    <a style="left:410px">ABOUT US</a>
    <a style="left:489px">PARTNERS</a>
    <a style="left:570px">CAREER</a>
    <a style="left:636px">MEMBERSHIPS</a>
    <a style="left:737px">NEWS</a>
    <a style="left:792px">GALLERY</a>
    <a style="left:863px">CONTACTS</a>
  </nav>
</header>

<section class="abs hero" role="img" aria-label="Photo of a smiling businesswoman in glasses at an office with colleagues blurred behind">
  <h1>LHC is an effective women's initiative<br>for you!</h1>
  <div class="dots"><span class="on" style="left:477px"></span><span style="left:497px"></span><span style="left:517px"></span></div>
</section>

<h2 class="abs intro">AT VERO EOS ET ACCUSAMUS ET IUSTO ODIO DIGNISSIMOS DUCIMUS<br>QUI BLANDITIIS</h2>

<div class="abs card" style="left:113px">
  <div class="card-icon">
    <svg width="24" height="40" viewBox="0 0 24 40"><circle cx="12" cy="5" r="4.5" fill="#1f7fc4"/><path d="M4 11h16a3 3 0 0 1 3 3v10h-4v15h-4V28h-2v11H5V24H1V14a3 3 0 0 1 3-3z" fill="#1f7fc4"/></svg>
  </div>
  <h3>Memberships</h3>
  <p>At Ladies' Harbor Collective, we offer the<br>opportunity to connect with&nbsp; throughout the globe.</p>
</div>

<div class="abs card" style="left:536px">
  <div class="card-icon">
    <svg width="38" height="40" viewBox="0 0 38 40"><circle cx="11" cy="5" r="4.5" fill="#1f7fc4"/><path d="M3 11h16a3 3 0 0 1 3 3v10h-4v15h-4V28h-2v11H4V24H0V14a3 3 0 0 1 3-3z" fill="#1f7fc4"/><circle cx="30" cy="18" r="3" fill="#1f7fc4"/><path d="M25 22h10a2 2 0 0 1 2 2v7h-2.5v8h-2.5v-6h-2v6h-2.5v-8H25z" fill="#1f7fc4"/></svg>
  </div>
  <h3>LHC Leadership</h3>
  <p>Join these trailblazers to shorten your path to<br>success and camaraderie.</p>
</div>

<h2 class="abs who">WHO WE ARE</h2>
<p class="abs who-text">Ladies' Harbor Collective is an online women's initiative that promotes your business and visions through social engagement. We are here to help you form strategic&nbsp; partnerships with like-minded women around the world. End your solo journey by becoming a member of LHC. LHC also features a forum to promote the services, campaigns,<br>LHC is about women helping other women. Contact us for more information.</p>
<div class="abs read-more">READ MORE</div>

<footer>
  <div class="abs footer"></div>
  <div class="abs foot-brand">Ladies' Harbor Collective</div>
  <p class="abs foot-about">Ladies' Harbor Collective is an online women's initiative that promotes your visions through engagement.</p>
  <div class="social">
    <span style="left:81px"></span><span style="left:110px"></span><span style="left:138px"></span>
    <span style="left:166px"></span><span style="left:195px"></span><span style="left:224px"></span>
  </div>

  <h4 class="abs foot-title" style="left:277px">Latest Feeds</h4>
  <div class="abs tweet" style="top:984px"><span class="tweet-dot"></span><p>Merry Pixel Studio wishes you and your family a merry Christmas and a happy new!<br><span class="when">about 2 days ago</span></p></div>
  <div class="abs tweet" style="top:1052px"><span class="tweet-dot"></span><p>Merry Pixel Studio wishes you and your family a merry Christmas and a happy new!<br><span class="when">about 2 days ago</span></p></div>

  <h4 class="abs foot-title" style="left:512px">Recent Posts</h4>
  <div class="abs thumb" style="left:512px;top:988px;background:linear-gradient(135deg,#6fa5a8,#c9a48f)" role="img" aria-label="Post photo of a woman"></div>
  <div class="abs thumb" style="left:575px;top:988px;background:linear-gradient(135deg,#b9cbd6,#e3d2bf)" role="img" aria-label="Post photo of a woman"></div>
  <div class="abs thumb" style="left:638px;top:988px;background:linear-gradient(135deg,#5a4b3c,#c9b79a)" role="img" aria-label="Post photo of a woman"></div>
  <div class="abs thumb" style="left:512px;top:1045px;background:linear-gradient(135deg,#3f4a56,#a78d79)" role="img" aria-label="Post photo of a woman"></div>
  <div class="abs thumb" style="left:575px;top:1045px;background:linear-gradient(135deg,#8ba0ae,#d6b59b)" role="img" aria-label="Post photo of a woman"></div>
  <div class="abs thumb" style="left:638px;top:1045px;background:linear-gradient(135deg,#7f8ea0,#6a4b63)" role="img" aria-label="Post photo of a woman"></div>

  <h4 class="abs foot-title" style="left:718px">NewsLetter</h4>
  <p class="abs news-text">Subscribe to our newsletter to receive news,<br>updates, free stuff and new releases by<br>email. We don't do spam..</p>
  <div class="abs email">Enter your email address</div>
  <div class="abs subscribe">SUBSCRIBE</div>

  <div class="abs footer-bottom"></div>
  <div class="abs copyright">Copyright © 2014 LadiesHarbor.COM</div>
  <nav class="foot-nav">
    <a style="left:506px">HOME</a>
    <a style="left:547px">ABOUT US</a>
    <a style="left:605px">PARTNERS</a>
    <a style="left:665px">CAREER</a>
    <a style="left:712px">MEMBERSHIPS</a>
    <a style="left:787px">NEWS</a>
    <a style="left:826px">GALLERY</a>
    <a style="left:877px">CONTACTS</a>
  </nav>
</footer>
</body>
</html>
```